13 Varno - new website design project

Our company Varno Electrical is developing a new lead generation website focused on Electrical, LED Lighting and Solar Power. We need a high converting website.

Example of our current website is www.varnoelectrical-example.com.au You can take content from this website for this new design. Our colours are red, black and white. For our new website we would like to promote Varno, Spark Every Day. Please listen to the jingle.

The below link is the company jingle that we have developed.
http://www.tunecraftdemo.com.au/vrn-tc-v1/

The key for this brief is to generate leads for Electrical, LED Lighting (for commercial) and Solar Power & Storage.

Target Market(s)

Business owners in Melbourne Victoria

Number of Pages Required

4 page

Colors
ec1f27
ffffff

Requirements
Must have
• This page must be clean, be in line with company branding and a high converting lead website.

```html
<!DOCTYPE html>
<html lang="en">
<head>
<meta charset="utf-8">
<title>Varno Electrical</title>
<link href="https://fonts.googleapis.com/css2?family=Roboto:wght@400;500;700&family=Roboto+Condensed:wght@400;700&display=swap" rel="stylesheet">
<style>
:root{
  --red:#ec1f27;
  --dark:#2b2d38;
  --ink:#222;
  --text:#444;
  --light:#f1f1f1;
  --white:#fff;
  --line:#d6d6d6;
}
*{box-sizing:border-box;margin:0;padding:0}
html,body{width:1200px;height:3711px;overflow:hidden;background:var(--white)}
body{position:relative;font-family:"Roboto",Arial,sans-serif;color:var(--text)}
.abs{position:absolute}
.brand{left:82px;top:14px;width:190px}
.brand-name{font-family:"Roboto Condensed",Arial,sans-serif;font-weight:700;font-size:50px;line-height:52px;color:var(--ink);display:flex;align-items:center;gap:10px}
.brand-name .dot{width:18px;height:18px;border-radius:50%;background:var(--red)}
.brand-tag{font-size:14px;color:var(--dark);margin-top:2px;letter-spacing:.3px}
.topbar{right:84px;top:20px;display:flex;align-items:center;gap:10px;font-size:13px;color:var(--ink)}
.topbar .ico{width:30px;height:30px;border:2px solid var(--red);border-radius:50%;display:flex;align-items:center;justify-content:center}
.topbar .gap{width:18px}
.social{width:30px;height:30px;border-radius:50%;background:var(--red)}
.nav{left:371px;top:82px;width:829px;height:47px;background:var(--dark);display:flex;align-items:center}
.nav a{flex:1;text-align:center;color:var(--white);font-family:"Roboto Condensed",Arial,sans-serif;font-weight:700;font-size:16px;text-decoration:none;border-right:1px solid #474a57;line-height:47px}
.nav a.active span{background:var(--red);border-radius:16px;padding:6px 24px}
.nav a:last-child{border:none}
.redline{left:0;top:126px;width:1200px;height:3px;background:var(--red)}
.hero{left:0;top:129px;width:1200px;height:588px;background:linear-gradient(180deg,#7d7c78 0%,#9a8f7c 35%,#6f655a 70%,#554d44 100%)}
.hero-disc{left:710px;top:240px;width:410px;height:410px;border-radius:50%;background:rgba(40,42,50,.72)}
.hero-title{left:740px;top:380px;width:350px;text-align:center;color:var(--white);font-family:"Roboto Condensed",Arial,sans-serif;font-weight:700;font-size:31px;line-height:38px}
.dots{display:flex;gap:8px}
.dots i{width:11px;height:11px;border-radius:50%;background:#ccc;display:block}
.dots i.on{background:var(--red)}
.sec-title{left:0;width:1200px;text-align:center;font-family:"Roboto Condensed",Arial,sans-serif;font-weight:700;font-size:33px;color:var(--ink);letter-spacing:.5px}
.sec-title em{font-style:normal;color:var(--red)}
.rule{width:58px;height:3px;background:var(--red)}
.svc{top:858px;width:328px;height:270px}
.svc-head{height:69px;background:var(--dark);border-radius:10px 10px 0 0;color:var(--white);font-family:"Roboto Condensed",Arial,sans-serif;font-weight:700;font-size:21px;text-align:center;line-height:69px}
.svc-img{height:185px}
.btn{display:inline-flex;align-items:center;gap:10px;background:var(--red);color:var(--white);border-radius:16px;height:31px;padding:0 6px 0 18px;font-family:"Roboto Condensed",Arial,sans-serif;font-weight:700;font-size:14px}
.btn .arr{width:23px;height:23px;border-radius:50%;background:var(--dark);display:flex;align-items:center;justify-content:center}
.svc .btn{position:absolute;left:82px;top:242px}
.about-img{left:0;top:1197px;width:599px;height:456px;background:linear-gradient(180deg,#c9ccd0,#9ea2a7 60%,#7a7d80)}
.about-bg{left:599px;top:1197px;width:601px;height:456px;background:var(--light)}
.about-title{left:638px;top:1246px;font-family:"Roboto Condensed",Arial,sans-serif;font-weight:700;font-size:33px;color:var(--ink)}
.about-title em{font-style:normal;color:var(--red)}
.about-copy{left:638px;top:1325px;width:520px;font-size:15px;line-height:22px;text-align:justify;color:var(--text)}
.about-copy p+p{margin-top:12px}
.why{width:300px;text-align:center}
.why h3{font-size:19px;font-weight:700;color:var(--ink);margin-bottom:10px}
.why p{font-size:13.5px;line-height:19px;color:var(--text)}
.why .go{width:24px;height:24px;border-radius:50%;margin:14px auto 0;display:flex;align-items:center;justify-content:center}
.work-bg{left:0;top:2405px;width:1200px;height:670px;background:var(--light)}
.work{top:2563px;width:330px;height:403px;background:var(--white);border:1px solid var(--line)}
.work-logo{height:70px;display:flex;align-items:center;justify-content:center;font-family:"Roboto",Arial,sans-serif;font-weight:700;font-size:30px}
.work-img{height:143px;position:relative}
.zoom{position:absolute;right:10px;bottom:8px;width:34px;height:34px;border-radius:50%;background:rgba(255,255,255,.85);display:flex;align-items:center;justify-content:center}
.work-body{padding:14px 14px}
.work-body h4{font-size:17px;color:var(--ink);font-weight:700}
.work-body .role{font-size:14px;color:var(--text);margin:6px 0 10px}
.work-body p{font-size:14px;line-height:20px;color:var(--text)}
.client{top:3211px;width:215px;height:97px;display:flex;align-items:center;justify-content:center;font-family:"Roboto",Arial,sans-serif;font-weight:700;font-size:26px;text-align:center;line-height:28px}
.footer{left:0;top:3370px;width:1200px;height:297px;background:var(--dark)}
.fhead{top:3414px;font-family:"Roboto Condensed",Arial,sans-serif;font-weight:700;font-size:17px;color:var(--white)}
.fhead em{font-style:normal;color:var(--red)}
.fdiv{top:3410px;width:1px;height:220px;background:#474a57}
.flinks{left:82px;top:3458px;list-style:none;font-size:13px;color:var(--white)}
.flinks li{margin-bottom:14px}
.flinks li:before{content:"• ";color:var(--white)}
.flinks li.on{color:var(--red)}
.fcontact{left:287px;top:3456px;color:var(--white);font-size:12.5px;width:275px}
.fcontact .row{display:flex;gap:10px;margin-bottom:18px;line-height:18px}
.fcontact .row div{white-space:nowrap}
.fcontact svg{flex:none;margin-top:2px}
.field{left:609px;width:264px;height:35px;border:1px solid #8a8c96;color:var(--white);font-size:13px;padding:8px 10px}
.flogo{left:965px;top:3440px;width:170px;text-align:center;color:var(--white)}
.flogo .brand-name{color:var(--white);justify-content:center}
.fsocial{display:flex;gap:10px;justify-content:center;margin-top:16px}
.fsocial .social{width:28px;height:28px}
.bottombar{left:0;top:3667px;width:1200px;height:44px;background:var(--red);color:var(--white);font-size:13px;display:flex;align-items:center;justify-content:space-between;padding:0 82px}
</style>
</head>
<body>

<div class="abs brand">
  <div class="brand-name"><span class="dot"></span>VARNO</div>
  <div class="brand-tag">Spark Every Day</div>
</div>
<div class="abs topbar">
  <span class="ico"><svg width="14" height="14" viewBox="0 0 24 24"><path fill="#ec1f27" d="M6.6 10.8a15 15 0 006.6 6.6l2.2-2.2c.3-.3.7-.4 1-.2 1.1.4 2.3.6 3.6.6.6 0 1 .4 1 1V20c0 .6-.4 1-1 1A17 17 0 013 4c0-.6.4-1 1-1h3.5c.6 0 1 .4 1 1 0 1.3.2 2.5.6 3.6.1.3 0 .7-.2 1z"/></svg></span>
  <span>130 555</span>
  <span class="gap"></span>
  <span class="ico"><svg width="14" height="14" viewBox="0 0 24 24"><path fill="#ec1f27" d="M3 5h18v14H3z M3 5l9 7 9-7" stroke="#fff" stroke-width="1.5"/></svg></span>
  <span>service@varnoelectrical-example.com.au</span>
  <span class="gap"></span>
  <span class="social"></span><span class="social"></span><span class="social"></span>
</div>
<nav class="abs nav">
  <a class="active"><span>HOME</span></a>
  <a>VARNO STORY</a>
  <a>SERVICES</a>
  <a>OUR WORK</a>
  <a>CONTACT US</a>
</nav>
<div class="abs redline"></div>

<div class="abs hero" role="img" aria-label="Photo of a large electrical warehouse with racking and stock"></div>
<div class="abs hero-disc"></div>
<div class="abs hero-title">Australia's largest fully integrated Electrical &amp; Energy Solutions Provider.</div>
<div class="abs dots" style="left:893px;top:571px"><i class="on"></i><i></i><i></i></div>

<div class="abs sec-title" style="top:758px">OUR <em>SERVICES</em></div>
<div class="abs rule" style="left:571px;top:812px"></div>

<div class="abs svc" style="left:82px">
  <div class="svc-head">ELECTRICAL</div>
  <div class="svc-img" role="img" aria-label="Photo of an electrician working on a switchboard" style="background:linear-gradient(135deg,#3c5b8c,#7b8aa0 50%,#c8ccd2)"></div>
  <span class="btn">READ MORE <span class="arr"><svg width="10" height="10" viewBox="0 0 10 10"><path d="M3 1l4 4-4 4" stroke="#fff" stroke-width="2" fill="none"/></svg></span></span>
</div>
<div class="abs svc" style="left:436px">
  <div class="svc-head">LED LIGHTING</div>
  <div class="svc-img" role="img" aria-label="Photo of LED light bulbs" style="background:linear-gradient(135deg,#b8bcc0,#e7e8ea 50%,#9fa3a8)"></div>
  <span class="btn">READ MORE <span class="arr"><svg width="10" height="10" viewBox="0 0 10 10"><path d="M3 1l4 4-4 4" stroke="#fff" stroke-width="2" fill="none"/></svg></span></span>
</div>
<div class="abs svc" style="left:792px">
  <div class="svc-head">SOLAR POWER</div>
  <div class="svc-img" role="img" aria-label="Photo of an installer fitting solar panels on a roof" style="background:linear-gradient(160deg,#5a8fd0,#2d4f8c 55%,#1d2f55)"></div>
  <span class="btn">READ MORE <span class="arr"><svg width="10" height="10" viewBox="0 0 10 10"><path d="M3 1l4 4-4 4" stroke="#fff" stroke-width="2" fill="none"/></svg></span></span>
</div>

<div class="abs about-img" role="img" aria-label="Photo of a bright factory floor lit by high-bay lighting"></div>
<div class="abs about-bg"></div>
<div class="abs about-title">ABOUT <em>VARNO</em></div>
<div class="abs rule" style="left:638px;top:1300px"></div>
<div class="abs about-copy">
  <p>Varno Electrical was formed to be an expert Electricity Contracting Company providing services to all Residential and Commercial Customers. With over 10 years of experience, Varno Electrical has developed a highly-experienced team of professionals that ensure all our customer expectations are met.</p>
  <p>Lorem ipsum dolor sit amet, consectetuer adipiscing elit, sed diam nonummy nibh euismod tincidunt ut laoreet dolore magna aliquam erat volutpat. Ut wisi enim ad minim veniam.</p>
</div>
<span class="abs btn" style="left:638px;top:1558px">READ MORE <span class="arr"><svg width="10" height="10" viewBox="0 0 10 10"><path d="M3 1l4 4-4 4" stroke="#fff" stroke-width="2" fill="none"/></svg></span></span>

<div class="abs sec-title" style="top:1692px">WHY <em>CHOOSE US?</em></div>
<div class="abs rule" style="left:571px;top:1746px"></div>

<div class="abs why" style="left:60px;top:1796px">
  <h3>Professional Service</h3>
  <p>When you hire a Varno Electrical Electrician you will get a professional and well-presented Electrician that comes skilled and ready to do the job.</p>
  <div class="go" style="background:var(--red)"><svg width="10" height="10" viewBox="0 0 10 10"><path d="M3 1l4 4-4 4" stroke="#fff" stroke-width="2" fill="none"/></svg></div>
</div>
<div class="abs why" style="left:446px;top:1796px">
  <h3>Value for Money</h3>
  <p>We provide extremely competitive pricing, which means you get value for money on quality that is comparable to the best in the industry.</p>
  <div class="go" style="background:var(--red)"><svg width="10" height="10" viewBox="0 0 10 10"><path d="M3 1l4 4-4 4" stroke="#fff" stroke-width="2" fill="none"/></svg></div>
</div>
<div class="abs why" style="left:840px;top:1796px">
  <h3>Fully insured</h3>
  <p>Varno Electrical is fully insured and equipped to handle break downs and service call outs.</p>
  <div class="go" style="background:var(--red)"><svg width="10" height="10" viewBox="0 0 10 10"><path d="M3 1l4 4-4 4" stroke="#fff" stroke-width="2" fill="none"/></svg></div>
</div>

<svg class="abs" style="left:0;top:1960px" width="1200" height="260" viewBox="0 0 1200 260">
  <g>
    <path d="M82 126 A121 121 0 0 0 324 126 L282 126 A79 79 0 0 1 124 126Z" fill="#ec1f27"/>
    <path d="M475 126 A121 121 0 0 0 717 126 L675 126 A79 79 0 0 1 517 126Z" fill="#ec1f27"/>
    <path d="M876 126 A121 121 0 0 0 1118 126 L1076 126 A79 79 0 0 1 918 126Z" fill="#ec1f27"/>
    <path d="M275 126 A121 121 0 0 1 517 126 L475 126 A79 79 0 0 0 317 126Z" fill="#2b2d38"/>
    <path d="M676 126 A121 121 0 0 1 918 126 L876 126 A79 79 0 0 0 718 126Z" fill="#2b2d38"/>
  </g>
  <g fill="#fff" stroke="#dadada" stroke-width="5">
    <circle cx="203" cy="126" r="72"/>
    <circle cx="396" cy="126" r="72"/>
    <circle cx="596" cy="126" r="72"/>
    <circle cx="797" cy="126" r="72"/>
    <circle cx="997" cy="126" r="72"/>
  </g>
  <g fill="#2b2d38">
    <circle cx="196" cy="110" r="11"/>
    <path d="M176 146 q0-22 20-22 q14 0 18 10 l-4 12z"/>
    <circle cx="218" cy="139" r="9"/>
    <circle cx="218" cy="139" r="3.5" fill="#fff"/>
  </g>
  <g fill="#2b2d38">
    <path d="M384 132 l-8 26 10-4 6 8 6-20z M408 132 l8 26-10-4-6 8-6-20z"/>
    <circle cx="396" cy="118" r="20"/>
    <circle cx="396" cy="118" r="14" fill="#fff"/>
    <path d="M396 108 l3 7 7 .5-5.5 4.5 2 7-6.5-4-6.5 4 2-7-5.5-4.5 7-.5z"/>
  </g>
  <g fill="#2b2d38">
    <path d="M586 98 h20 l-5 10 h-10z"/>
    <path d="M590 110 h12 q22 16 18 36 q-2 8-14 8 h-20 q-12 0-14-8 q-4-20 18-36z"/>
    <text x="596" y="145" font-family="Roboto,Arial,sans-serif" font-weight="700" font-size="24" fill="#fff" text-anchor="middle">$</text>
  </g>
  <g fill="none" stroke="#2b2d38" stroke-width="4">
    <circle cx="797" cy="126" r="22"/>
    <ellipse cx="797" cy="126" rx="10" ry="22"/>
    <path d="M775 126 h44"/>
  </g>
  <g>
    <path d="M997 100 l22 8 v16 q0 20-22 30 q-22-10-22-30 v-16z" fill="none" stroke="#2b2d38" stroke-width="4"/>
    <path d="M987 127 l7 7 13-14" fill="none" stroke="#2b2d38" stroke-width="5"/>
  </g>
</svg>

<div class="abs why" style="left:246px;top:2188px">
  <h3>5 year workmanship guarantee</h3>
  <p>You can buy with confidence as all of our work has a 5 year workmanship guarantee. For your peace of mind, we unconditionally back our electrical work. We will come back to fix any problems at our own expense.</p>
  <div class="go" style="background:var(--dark)"><svg width="10" height="10" viewBox="0 0 10 10"><path d="M3 1l4 4-4 4" stroke="#fff" stroke-width="2" fill="none"/></svg></div>
</div>
<div class="abs why" style="left:647px;top:2188px">
  <h3>Environmentally friendly</h3>
  <p>We a committed to reducing carbon emissions by installing Solar Power and upgrading sites to LED Lighting. In addition to reducing the carbon emissions we recycle Fluorescent Tubes, Highbay Globes, Metal and Cardboard</p>
  <div class="go" style="background:var(--dark)"><svg width="10" height="10" viewBox="0 0 10 10"><path d="M3 1l4 4-4 4" stroke="#fff" stroke-width="2" fill="none"/></svg></div>
</div>

<div class="abs work-bg"></div>
<div class="abs sec-title" style="top:2455px">OUR <em>WORK</em></div>
<div class="abs rule" style="left:571px;top:2509px"></div>

<div class="abs work" style="left:82px">
  <div class="work-logo" style="background:#f6e500;color:#222">Outback Gear Depot</div>
  <div class="work-img" role="img" aria-label="Photo of a lit retail store frontage" style="background:linear-gradient(180deg,#8c8d90,#5e5f63)"><span class="zoom"><svg width="18" height="18" viewBox="0 0 20 20"><circle cx="8" cy="8" r="6" stroke="#333" stroke-width="2" fill="none"/><path d="M12.5 12.5l5 5M5 8h6M8 5v6" stroke="#333" stroke-width="2"/></svg></span></div>
  <div class="work-body">
    <h4>Jamie Harlow</h4>
    <div class="role">Executive Outback Gear Depot</div>
    <p>The service, communication and after sales service of Varno Electrical has been awesome. We would strongly recommend them to any business contemplating upgrading.</p>
  </div>
</div>
<div class="abs work" style="left:436px">
  <div class="work-logo" style="color:var(--red);font-weight:400">Duskhaven</div>
  <div class="work-img" role="img" aria-label="Photo of a bright shop interior after a lighting upgrade" style="background:linear-gradient(180deg,#d7d8dc,#9a8f95)"><span class="zoom"><svg width="18" height="18" viewBox="0 0 20 20"><circle cx="8" cy="8" r="6" stroke="#333" stroke-width="2" fill="none"/><path d="M12.5 12.5l5 5M5 8h6M8 5v6" stroke="#333" stroke-width="2"/></svg></span></div>
  <div class="work-body">
    <h4>C. Marlo</h4>
    <div class="role">Balwyn North VIC</div>
    <p>They clean up after the job, explained everything I needed to know and answered all questions, very professional. Will use them again in the future!</p>
  </div>
</div>
<div class="abs work" style="left:792px">
  <div class="work-logo" style="color:#1f6fb5;font-weight:400">Steelmark</div>
  <div class="work-img" role="img" aria-label="Photo of a steel storage warehouse" style="background:linear-gradient(180deg,#a9adb2,#5d6166)"><span class="zoom"><svg width="18" height="18" viewBox="0 0 20 20"><circle cx="8" cy="8" r="6" stroke="#333" stroke-width="2" fill="none"/><path d="M12.5 12.5l5 5M5 8h6M8 5v6" stroke="#333" stroke-width="2"/></svg></span></div>
  <div class="work-body">
    <h4>B. Worley</h4>
    <div class="role">Cranbourne North VIC</div>
    <p>Excellent work and very professional. Anthony takes time to explain everything and demonstrate workings. Very clear precise and accurate.</p>
  </div>
</div>
<div class="abs dots" style="left:575px;top:3002px"><i class="on"></i><i style="background:#2b2d38"></i><i style="background:#2b2d38"></i></div>

<div class="abs sec-title" style="top:3108px">OUR SATISFIED <em>CLIENTS</em></div>
<div class="abs rule" style="left:571px;top:3162px"></div>
<div class="abs client" style="left:129px;color:var(--red);font-weight:400;font-size:34px">Duskhaven</div>
<div class="abs client" style="left:371px;background:#f6e500;color:#222">Outback Gear Depot</div>
<div class="abs client" style="left:614px;background:var(--red);color:#fff">Heron Plumbing</div>
<div class="abs client" style="left:856px;background:#d5161d;color:#fff">Burgerline</div>

<div class="abs footer"></div>
<div class="abs fhead" style="left:82px">QUICK <em>LINKS</em></div>
<div class="abs fhead" style="left:287px">CONTACT <em>DETAILS</em></div>
<div class="abs fhead" style="left:606px">QUICK <em>INQUIRY</em></div>
<div class="abs fdiv" style="left:240px"></div>
<div class="abs fdiv" style="left:575px"></div>
<div class="abs fdiv" style="left:920px"></div>
<ul class="abs flinks">
  <li class="on">Home</li>
  <li>Varno Story</li>
  <li>Services</li>
  <li>Our Work</li>
  <li>Contact Us</li>
</ul>
<div class="abs fcontact">
  <div class="row"><svg width="14" height="18" viewBox="0 0 14 18"><path d="M7 0a7 7 0 017 7c0 5-7 11-7 11S0 12 0 7a7 7 0 017-7z" fill="#ec1f27"/><circle cx="7" cy="7" r="2.5" fill="#2b2d38"/></svg><div><b>Varno</b><br>14/220 Ferndale Rd, Mount<br>Ridley, VIC 3199</div></div>
  <div class="row"><svg width="14" height="14" viewBox="0 0 24 24"><path fill="#ec1f27" d="M6.6 10.8a15 15 0 006.6 6.6l2.2-2.2c.3-.3.7-.4 1-.2 1.1.4 2.3.6 3.6.6.6 0 1 .4 1 1V20c0 .6-.4 1-1 1A17 17 0 013 4c0-.6.4-1 1-1h3.5c.6 0 1 .4 1 1 0 1.3.2 2.5.6 3.6.1.3 0 .7-.2 1z"/></svg><div>130 555</div></div>
  <div class="row"><svg width="14" height="12" viewBox="0 0 14 12"><rect width="14" height="12" fill="#ec1f27"/><path d="M0 0l7 6 7-6" stroke="#2b2d38" stroke-width="1.5" fill="none"/></svg><div>service@varnoelectrical-example.com.au</div></div>
</div>
<div class="abs field" style="top:3458px">Name</div>
<div class="abs field" style="top:3500px">Email</div>
<div class="abs field" style="top:3542px;height:48px">Message</div>
<span class="abs btn" style="left:609px;top:3601px;height:27px;font-size:12px">SUBMIT <span class="arr" style="width:19px;height:19px"><svg width="8" height="8" viewBox="0 0 10 10"><path d="M3 1l4 4-4 4" stroke="#fff" stroke-width="2" fill="none"/></svg></span></span>
<div class="abs flogo">
  <div class="brand-name"><span class="dot"></span>VARNO</div>
  <div class="brand-tag" style="color:#fff">Spark Every Day</div>
  <div class="fsocial"><span class="social"></span><span class="social"></span><span class="social"></span></div>
</div>
<div class="abs bottombar">
  <span>Copyright © 2017 Varno. All Right Reserved.</span>
  <span>Terms and Conditions &nbsp;|&nbsp; Privacy</span>
</div>

</body>
</html>
```